Thornvale Group needs a business card design

We need a new business card design using the logo recently selected in a logo competition on Pixel Bazaar. Our business is a consultancy specializing in aviation and energy and the winning business card design will promote an image of precision and professionalism with creativity.

Please use the logo with the name on the front of the card and use a complementary font. Make the back white with either the light grey or dark grey logo.

Target Market(s)

Senior finance and legal leaders at aviation and energy companies

Industry/Entity Type

Management Consulting

Contact Information for Business Card

Peter Castrell
President
Thornvale Group

www.thornvalegroup.example

(555) 204-6391
pc@thornvalegroup.example

Requirements
Must have
• Professional font that goes well with the logo font

```html
<!DOCTYPE html>
<html lang="en">
<head>
<meta charset="utf-8">
<title>Thornvale Group – Business Card</title>
<link href="https://fonts.googleapis.com/css2?family=Raleway:wght@300;400&display=swap" rel="stylesheet">
<style>
  :root {
    --backdrop: #8e8f91;
    --navy: #0d3563;
    --paper: #e7e8ec;
    --on-navy: #e9ebf0;
    --grey-type: #6b6c70;
  }
  html, body {
    margin: 0;
    padding: 0;
    width: 1105px;
    height: 1200px;
    overflow: hidden;
    background: var(--backdrop);
    font-family: "Raleway", sans-serif;
  }
  .canvas {
    position: relative;
    width: 1105px;
    height: 1200px;
  }
  .card {
    position: absolute;
    left: 182px;
    width: 747px;
    height: 427px;
    overflow: hidden;
  }
  .card--front {
    top: 119px;
    background: var(--navy);
    color: var(--on-navy);
  }
  .card--back {
    top: 636px;
    background: var(--paper);
  }
  .brand-square {
    position: absolute;
    background: var(--paper);
  }
  .brand-square--front {
    left: 70px;
    top: 110px;
    width: 200px;
    height: 200px;
  }
  .brand-square--back {
    left: 333px;
    top: 122px;
    width: 82px;
    height: 82px;
    background: var(--navy);
  }
  .line {
    position: absolute;
    right: 39px;
    margin: 0;
    line-height: 1;
    white-space: nowrap;
    text-align: right;
    font-weight: 300;
  }
  .wordmark {
    top: 34px;
    font-size: 53px;
    letter-spacing: 2px;
  }
  .wordmark-sub {
    top: 86px;
    right: 39px;
    font-size: 21px;
    letter-spacing: 42px;
    margin-right: -42px;
  }
  .person-name { top: 137px; font-size: 29px; font-weight: 400; letter-spacing: 0.5px; }
  .person-role { top: 171px; font-size: 21px; }
  .company { top: 208px; font-size: 19px; }
  .service { top: 239px; font-size: 19px; }
  .sectors { top: 268px; font-size: 19px; }
  .contact {
    display: flex;
    align-items: center;
    gap: 10px;
    font-size: 19px;
  }
  .contact--phone { top: 305px; }
  .contact--email { top: 337px; }
  .contact--web { top: 368px; }
  .contact svg { width: 18px; height: 18px; flex: none; }

  .back-mark {
    position: absolute;
    left: 0;
    right: 0;
    text-align: center;
    margin: 0;
    line-height: 1;
    font-weight: 300;
  }
  .back-mark--name {
    top: 245px;
    font-size: 49px;
    letter-spacing: 2px;
    color: var(--navy);
  }
  .back-mark--sub {
    top: 301px;
    font-size: 20px;
    letter-spacing: 38px;
    padding-left: 38px;
    color: var(--grey-type);
  }
</style>
</head>
<body>
<main class="canvas">
  <section class="card card--front" aria-label="Card front">
    <div class="brand-square brand-square--front" role="img" aria-label="Brand mark area"></div>
    <p class="line wordmark">THORNVALE</p>
    <p class="line wordmark-sub">GROUP</p>
    <p class="line person-name">PETER CASTRELL</p>
    <p class="line person-role">President</p>
    <p class="line company">Thornvale Group LLC</p>
    <p class="line service">Finance and Strategy Consulting</p>
    <p class="line sectors">Aviation - Manufacturing - Energy</p>
    <p class="line contact contact--phone">(555) 204-6391
      <svg viewBox="0 0 24 24" aria-hidden="true"><path fill="currentColor" d="M6.6 10.8a15 15 0 0 0 6.6 6.6l2.2-2.2c.3-.3.7-.4 1-.2 1.1.4 2.3.6 3.6.6.6 0 1 .4 1 1V20c0 .6-.4 1-1 1A17 17 0 0 1 3 4c0-.6.4-1 1-1h3.5c.6 0 1 .4 1 1 0 1.3.2 2.5.6 3.6.1.3 0 .7-.2 1z"/></svg>
    </p>
    <p class="line contact contact--email">pc@thornvalegroup.example
      <svg viewBox="0 0 24 24" aria-hidden="true"><rect x="2" y="5" width="20" height="14" rx="1" fill="currentColor"/><path d="M3 6l9 7 9-7" fill="none" stroke="#0d3563" stroke-width="1.6"/></svg>
    </p>
    <p class="line contact contact--web">thornvalegroup.example
      <svg viewBox="0 0 24 24" aria-hidden="true"><circle cx="12" cy="12" r="10" fill="currentColor"/><path d="M12 2c-3 3-3 17 0 20M12 2c3 3 3 17 0 20M2.5 12h19M4 7h16M4 17h16" fill="none" stroke="#0d3563" stroke-width="1.3"/></svg>
    </p>
  </section>

  <section class="card card--back" aria-label="Card back">
    <div class="brand-square brand-square--back" role="img" aria-label="Brand mark area"></div>
    <p class="back-mark back-mark--name">THORNVALE</p>
    <p class="back-mark back-mark--sub">GROUP</p>
  </section>
</main>
</body>
</html>
```